Business Card for Vorla Parts Wholesale supplier

Hi There! I need a new business card for our company. We are specialized in selling Vorla parts, mostly we sell new LCD screens for Zelnar and Drelks. I would like to see that back in the design.

You can find the colors and logo's on our website: www.hartuvo.nl

Industry/Entity Type

Business

Contact Information for Business Card

My Details:
Tobias Lindqvist

Phone: 0031687203316
E-mail: Tobias@hartuvo.nl

Slogan: "Because Quality Matters"

Font styles to use
Sans Serif

Colors

Designer to choose colors to be used in the design.

Requirements
Must have
• A Black backside with the Hartuvo logo on it. The front side should be clean with only my contact details.
• But I'm also open for something really different or awesome!
Nice to have
• Remember that we are in the parts & repairing industry, So i'll be handing those business cards mainly to repair companies. Maybe you can do something with that thought :)

```html
<!DOCTYPE html>
<html lang="en">
<head>
<meta charset="utf-8">
<title>Hartuvo Business Card</title>
<link href="https://fonts.googleapis.com/css2?family=Open+Sans:wght@400;600;700&display=swap" rel="stylesheet">
<style>
  :root {
    --backdrop: #4a423d;
    --card-white: #fbfbfa;
    --card-black: #050505;
    --ink: #111111;
    --orange: #f47a20;
    --peach: #f7e6d9;
    --shade: #141414;
    --white: #ffffff;
  }
  * { box-sizing: border-box; margin: 0; padding: 0; }
  html, body {
    width: 1200px;
    height: 844px;
    overflow: hidden;
  }
  body {
    background: var(--backdrop);
    font-family: "Open Sans", sans-serif;
    position: relative;
  }
  .card {
    position: absolute;
    top: 268px;
    width: 540px;
    height: 309px;
    overflow: hidden;
    box-shadow: 0 10px 24px rgba(0, 0, 0, 0.35);
  }
  .card--front { left: 40px; background: var(--card-white); }
  .card--back  { left: 620px; background: var(--card-black); }

  .brand {
    position: absolute;
    display: flex;
    align-items: center;
  }
  .brand__dot {
    border-radius: 50%;
    background: var(--orange);
    flex: none;
  }
  .brand__name {
    font-weight: 700;
    letter-spacing: 0.5px;
    line-height: 1;
  }

  .card--front .brand { left: 32px; top: 70px; gap: 16px; }
  .card--front .brand__dot { width: 64px; height: 64px; }
  .card--front .brand__name { font-size: 74px; color: var(--ink); }

  .card--back .brand { right: 34px; top: 140px; gap: 10px; }
  .card--back .brand__dot { width: 30px; height: 30px; }
  .card--back .brand__name { font-size: 34px; color: var(--white); }

  .decor-ring {
    position: absolute;
    border-radius: 50%;
  }
  .card--front .decor-ring {
    width: 200px; height: 200px;
    right: 20px; top: 100px;
    border: 38px solid var(--peach);
  }
  .card--back .decor-ring {
    width: 280px; height: 280px;
    left: -50px; top: 20px;
    border: 54px solid var(--shade);
  }

  .contact {
    position: absolute;
    left: 34px;
    bottom: 26px;
    color: var(--ink);
    font-size: 13px;
    line-height: 1.55;
  }
  .contact__name {
    color: var(--orange);
    font-weight: 600;
    font-size: 17px;
    letter-spacing: 0.4px;
    text-transform: uppercase;
    margin-bottom: 2px;
  }
  .contact__label { color: var(--orange); font-weight: 600; }
  .contact__sep { margin: 0 6px; }
  .contact__web { color: var(--orange); font-weight: 700; }
  .contact__slogan {
    margin-top: 10px;
    font-size: 14px;
    font-weight: 600;
    text-transform: uppercase;
    letter-spacing: 0.3px;
  }
</style>
</head>
<body>
  <section class="card card--front" aria-label="Business card front">
    <div class="decor-ring" aria-hidden="true"></div>
    <div class="brand">
      <span class="brand__dot" aria-hidden="true"></span>
      <span class="brand__name">hartuvo</span>
    </div>
    <div class="contact">
      <p class="contact__name">Tobias Lindqvist</p>
      <p><span class="contact__label">P:</span> 0031687203316<span class="contact__sep">|</span><span class="contact__label">E:</span> Tobias@hartuvo.nl</p>
      <p class="contact__web">www.hartuvo.nl</p>
      <p class="contact__slogan">Because Quality Matters</p>
    </div>
  </section>

  <section class="card card--back" aria-label="Business card back">
    <div class="decor-ring" aria-hidden="true"></div>
    <div class="brand">
      <span class="brand__dot" aria-hidden="true"></span>
      <span class="brand__name">hartuvo</span>
    </div>
  </section>
</body>
</html>
```